Duct Manufacturing Company new to the industry needs business card and stationary design

we are sheet metal duct manufacturers looking for a business card design to fit my new business logo.
nothing to crazy that will date, but want it to stand out from the crowed.
I'm sure you guys will work it out.

Contact Information for Business Card

Glen Marsh
Director

Address
17 Dorwell St
Carrowby NSW 2741

0438 760 514

Sales@flowbend.com.au

Font styles to use
Other font styles liked:
• BankGothic md bt

Requirements
Nice to have
• Like the idea of corner rounded to match logo
• like to keep colours flowing
• font I like sharp square not rounded

```html
<!DOCTYPE html>
<html lang="en">
<head>
<meta charset="utf-8">
<title>Flowbend Industries – Business Card</title>
<link rel="stylesheet" href="https://fonts.googleapis.com/css2?family=Michroma&display=swap">
<style>
  :root {
    --blue: #0b7cc4;
    --blue-deep: #0a6db4;
    --blue-light: #1590d4;
    --green: #8cc13f;
    --navy: #0b1f3a;
    --ink: #111111;
    --white: #ffffff;
    --backdrop: #e8e6e1;
  }
  * { box-sizing: border-box; margin: 0; padding: 0; }
  html, body {
    width: 1189px; height: 1200px; overflow: hidden;
    background: var(--backdrop);
    font-family: "Michroma", "Arial", sans-serif;
  }
  .canvas { position: relative; width: 1189px; height: 1200px; }
  .card {
    position: absolute; left: 171px; width: 856px; height: 487px;
    border-radius: 22px; overflow: hidden; background: var(--white);
    box-shadow: 0 6px 14px rgba(0,0,0,0.28);
  }
  .card--front { top: 68px; }
  .card--back { top: 626px; }

  .artwork { position: absolute; left: 0; right: 0; }
  .artwork--top {
    top: 0; height: 136px;
    background: linear-gradient(180deg, var(--blue-deep) 0%, var(--blue-light) 70%, var(--green) 100%);
  }
  .artwork--bottom {
    bottom: 0; height: 130px;
    background: linear-gradient(180deg, var(--green) 0%, var(--blue-light) 35%, var(--blue-deep) 100%);
  }
  .card--back .artwork--bottom { height: 135px; }

  .wordmark { position: absolute; color: var(--blue); text-transform: uppercase; line-height: 1; }
  .wordmark span { display: block; }
  .card--front .wordmark { left: 0; right: 0; top: 180px; text-align: center; }
  .card--front .wordmark__name { font-size: 66px; letter-spacing: 1px; }
  .card--front .wordmark__sub { font-size: 42px; letter-spacing: 14px; margin-top: 18px; padding-left: 14px; }

  .card--back .wordmark { left: 50px; top: 200px; }
  .card--back .wordmark__name { font-size: 40px; }
  .card--back .wordmark__sub { font-size: 27px; letter-spacing: 8px; margin-top: 10px; }

  .person { position: absolute; right: 44px; top: 88px; text-align: right; text-transform: uppercase; }
  .person__name { font-size: 27px; color: var(--blue-deep); letter-spacing: 5px; line-height: 1.1; }
  .person__role { font-size: 17px; color: var(--ink); letter-spacing: 3px; margin-top: 4px; }

  .contacts { position: absolute; right: 44px; top: 205px; list-style: none; }
  .contacts li {
    display: flex; justify-content: flex-end; align-items: center; gap: 10px;
    height: 29px; font-size: 16px; letter-spacing: 3px; color: var(--ink);
  }
  .contacts .icon { width: 24px; height: 24px; flex: none; }

  .address {
    position: absolute; right: 44px; top: 400px; text-align: right;
    font-size: 16px; letter-spacing: 3px; color: var(--navy); line-height: 31px;
  }
</style>
</head>
<body>
<div class="canvas">

  <section class="card card--front" aria-label="Business card front">
    <div class="artwork artwork--top" role="img" aria-label="Blue and green flowing band artwork"></div>
    <div class="wordmark">
      <span class="wordmark__name">Flowbend</span>
      <span class="wordmark__sub">Industries</span>
    </div>
    <div class="artwork artwork--bottom" role="img" aria-label="Green and blue flowing band artwork"></div>
  </section>

  <section class="card card--back" aria-label="Business card back">
    <div class="artwork artwork--bottom" role="img" aria-label="Green and blue flowing band artwork"></div>

    <div class="wordmark">
      <span class="wordmark__name">Flowbend</span>
      <span class="wordmark__sub">Industries</span>
    </div>

    <div class="person">
      <p class="person__name">Glen Marsh</p>
      <p class="person__role">Director</p>
    </div>

    <ul class="contacts">
      <li>0438 760 514
        <svg class="icon" viewBox="0 0 24 24" aria-hidden="true"><rect width="24" height="24" rx="4" fill="var(--green)"/><rect x="8" y="4" width="8" height="16" rx="1.5" fill="none" stroke="#fff" stroke-width="1.6"/><line x1="10" y1="17" x2="14" y2="17" stroke="#fff" stroke-width="1.4"/></svg>
      </li>
      <li>02 6184 3072
        <svg class="icon" viewBox="0 0 24 24" aria-hidden="true"><rect width="24" height="24" rx="4" fill="var(--green)"/><path d="M4 10 C4 6 20 6 20 10 L17 11 L16 9 H8 L7 11 Z" fill="#fff"/><path d="M7 12 H17 L18 19 H6 Z" fill="#fff"/><circle cx="12" cy="15" r="1.8" fill="var(--green)"/></svg>
      </li>
      <li>Sales@flowbend.com.au
        <svg class="icon" viewBox="0 0 24 24" aria-hidden="true"><rect width="24" height="24" rx="4" fill="var(--green)"/><rect x="4" y="7" width="16" height="11" fill="none" stroke="#fff" stroke-width="1.6"/><path d="M4 7 L12 13.5 L20 7" fill="none" stroke="#fff" stroke-width="1.6"/></svg>
      </li>
      <li>www.flowbend.com.au
        <svg class="icon" viewBox="0 0 24 24" aria-hidden="true"><rect width="24" height="24" rx="4" fill="var(--green)"/><circle cx="12" cy="12" r="7" fill="none" stroke="#fff" stroke-width="1.5"/><ellipse cx="12" cy="12" rx="3" ry="7" fill="none" stroke="#fff" stroke-width="1.2"/><line x1="5" y1="12" x2="19" y2="12" stroke="#fff" stroke-width="1.2"/></svg>
      </li>
    </ul>

    <p class="address">17 Dorwell St<br>Carrowby NSW 2741</p>
  </section>

</div>
</body>
</html>
```